HOT TUB - SPAS service needs an business card

I need an business for my company who his specialise in a maintenance,water treatment and cleaning of Hot Tub - Spas for commercial and residential customers. The company operate mainly in the ski resort of Chamonix, Megève and St Gervais. The final product should communicate pure water, cleanest and professional for luxury property's.
I have upload a logo but any improvement on it is welcome.(color,size, details etc..) or any other idea. Thank you
Company Name: 58 BAINS
My name: Lucien Marchetti
Email: lucimarch@examplemail.net
Tel: +33 (0)6 71 58 29 64
Description to be on the card in french(first langage) and in English:
- Spas service
- Entretien, traitement eau, nettoyage.
- Maintenance, water treatment, cleaning.
Industry/Entity Type
Residential
Colors
Designer to choose colors to be used in the design.
Look and feel
Each slider illustrates characteristics of the customer's brand and the style your logo design should communicate.

```html
<!DOCTYPE html>
<html lang="fr">
<head>
<meta charset="utf-8">
<title>58 BAINS – Business Card</title>
<link rel="stylesheet" href="https://fonts.googleapis.com/css2?family=Open+Sans:wght@400;600;700&display=swap">
<style>
  :root {
    --backdrop: #ece7df;
    --front-sky: #21a3f5;
    --front-deep: #0b62c9;
    --wave-light: #a9dcff;
    --back-blue: #0f78d8;
    --ink-white: #ffffff;
  }
  * { margin: 0; padding: 0; box-sizing: border-box; }
  html, body {
    width: 1200px; height: 1056px; overflow: hidden;
    background: var(--backdrop);
    font-family: "Open Sans", Arial, sans-serif;
    color: var(--ink-white);
  }
  .canvas { position: relative; width: 1200px; height: 1056px; }
  .card {
    position: absolute; border-radius: 24px; overflow: hidden;
    box-shadow: 0 4px 12px rgba(0,0,0,.18);
  }
  .card-front {
    left: 342px; top: 34px; width: 813px; height: 464px;
    background: var(--front-sky);
  }
  .front-waves { position: absolute; inset: 0; }
  .owner-name {
    position: absolute; right: 32px; top: 26px;
    font-size: 27px; font-weight: 700;
  }
  .company-name {
    position: absolute; left: 54px; top: 282px;
    font-size: 34px; font-weight: 700; letter-spacing: .5px;
  }
  .contact { position: absolute; left: 42px; font-size: 25px; font-weight: 400; display: flex; align-items: center; gap: 10px; }
  .contact-phone { top: 366px; font-weight: 600; }
  .contact-email { top: 408px; }
  .contact svg { width: 22px; height: 22px; }
  .card-back {
    left: 89px; top: 538px; width: 813px; height: 463px;
    background: var(--back-blue);
  }
  .brand-wordmark {
    position: absolute; left: 99px; top: 89px; width: 627px; height: 171px;
    display: flex; align-items: center; justify-content: center;
    font-size: 64px; font-weight: 700; letter-spacing: 3px;
    border-bottom: 2px solid var(--ink-white);
  }
  .services { position: absolute; left: 0; right: 0; top: 318px; text-align: center; }
  .services-title { font-size: 27px; font-weight: 700; margin-bottom: 8px; }
  .services-line { font-size: 27px; line-height: 40px; }
</style>
</head>
<body>
<main class="canvas">
  <section class="card card-front">
    <svg class="front-waves" viewBox="0 0 813 464" preserveAspectRatio="none" aria-hidden="true">
      <path d="M0 0 H813 V232 Q390 -10 0 108 Z" fill="var(--front-deep)"/>
      <path d="M0 108 Q390 -10 813 232 V262 Q390 12 0 134 Z" fill="var(--wave-light)"/>
      <path d="M0 134 Q390 12 813 262 V272 Q390 26 0 148 Z" fill="var(--front-sky)" opacity=".6"/>
      <path d="M0 96 Q390 -18 813 214" fill="none" stroke="#ffffff" stroke-width="2" opacity=".5"/>
    </svg>
    <div class="owner-name">Lucien Marchetti</div>
    <div class="company-name">58 BAINS</div>
    <div class="contact contact-phone">
      <svg viewBox="0 0 24 24" aria-hidden="true"><circle cx="12" cy="12" r="10.5" fill="none" stroke="#fff" stroke-width="1.8"/><path d="M9 6.5c-1.5.6-2 2.4-1 4.6 1.2 2.6 3 4.6 5.4 5.8 1.6.6 2.8.1 3.2-1l-2.2-1.6-1.2.9c-1.3-.7-2.5-2-3.2-3.4l.9-1.2z" fill="#fff"/></svg>
      <span>+33 (0)6 71 58 29 64</span>
    </div>
    <div class="contact contact-email">
      <svg viewBox="0 0 24 24" aria-hidden="true"><path d="M2 10 L12 3 L22 10 V21 H2 Z" fill="#fff"/><path d="M2 10 L12 16 L22 10" fill="none" stroke="#21a3f5" stroke-width="1.6"/></svg>
      <span>lucimarch@examplemail.net</span>
    </div>
  </section>

  <section class="card card-back">
    <div class="brand-wordmark">58 BAINS</div>
    <div class="services">
      <div class="services-title">SPAS SERVICES</div>
      <div class="services-line">• Entretien &nbsp;• traitement eau &nbsp;• nettoyage</div>
      <div class="services-line">• Maintenance &nbsp;• water treatment &nbsp;• cleaning.</div>
    </div>
  </section>
</main>
</body>
</html>
```